KBT Business Cards

We require business cards for our business. We would like a matte black back to the card, with our logo centred in the middle. The front side of the card is open to design.

Target Market(s)

Clients looking for legal services (professional)

Industry/Entity Type

Legal

Contact Information for Business Card

Doran Kelbrath
Partner
Mobile: 0461 738 524
Email: doran@kbtlaw.co
Website: www.kbtlaw.co
Level 3, 118 Wendmore Street
Sydney NSW 2000

Font styles to use
Other font styles liked:
• Avenir

Colors
f04a50
ffffff
1b1b1b

Requirements
Must have
• Black back with logo included in the centre of the card.
• Our font is Avenir.

```html
<!DOCTYPE html>
<html lang="en">
<head>
<meta charset="utf-8">
<title>KBT Business Cards</title>
<link href="https://fonts.googleapis.com/css2?family=Nunito+Sans:wght@400;600;700;800&display=swap" rel="stylesheet">
<style>
  :root {
    --red: #f04a50;
    --ink: #1b1b1b;
    --paper: #f6f6f6;
    --card-black: #262727;
    --stage: #202020;
    --silver: #c9c9c9;
  }
  * { box-sizing: border-box; margin: 0; padding: 0; }
  html, body { width: 980px; height: 1200px; overflow: hidden; background: var(--stage); }
  body { position: relative; font-family: "Nunito Sans", sans-serif; }

  .card { position: absolute; left: 126px; width: 757px; height: 432px; overflow: hidden; }
  .card-back { top: 102px; background: var(--card-black); }
  .card-front { top: 642px; background: var(--paper); color: var(--ink); }

  .brand { position: absolute; display: flex; align-items: center; }
  .brand-square { flex: none; }
  .brand-name { font-weight: 800; text-transform: uppercase; line-height: 1.02; }

  .card-back .brand { left: 50%; top: 50%; transform: translate(-50%, -50%); gap: 34px; }
  .card-back .brand-square { width: 96px; height: 96px; background: var(--silver); transform: rotate(45deg); }
  .card-back .brand-name { color: var(--silver); font-size: 42px; }

  .card-front .brand { right: 28px; top: 40px; gap: 22px; }
  .card-front .brand-square { width: 62px; height: 62px; background: var(--ink); transform: rotate(45deg); }
  .card-front .brand-name { color: var(--ink); font-size: 27px; }

  .person { position: absolute; left: 28px; top: 202px; }
  .person-bar { position: absolute; left: 0; top: 207px; width: 13px; height: 44px; background: var(--red); }
  .person-name { font-size: 27px; font-weight: 800; letter-spacing: 0.2px; text-transform: uppercase; line-height: 1; }
  .person-name .surname { color: var(--red); }
  .person-role { margin-top: 10px; font-size: 15px; letter-spacing: 1.6px; font-weight: 600; }

  .divider { position: absolute; left: 28px; top: 270px; width: 304px; height: 2px; background: var(--ink); }

  .contacts { position: absolute; left: 28px; top: 286px; list-style: none; font-size: 17px; letter-spacing: 1px; }
  .contacts li { display: flex; align-items: flex-start; gap: 14px; line-height: 23px; margin-bottom: 2px; }
  .contacts svg { flex: none; width: 16px; height: 16px; margin-top: 4px; fill: var(--red); }

  .footer-band { position: absolute; left: 0; bottom: 0; width: 757px; height: 12px; }
</style>
</head>
<body>

<section class="card card-back" aria-label="Card back">
  <div class="brand">
    <span class="brand-square"></span>
    <div class="brand-name">Kelbrath<br>Brandt Tolley<br>Legal</div>
  </div>
</section>

<section class="card card-front" aria-label="Card front">
  <div class="brand">
    <span class="brand-square"></span>
    <div class="brand-name">Kelbrath<br>Brandt Tolley<br>Legal</div>
  </div>

  <span class="person-bar"></span>
  <div class="person">
    <h1 class="person-name">Doran <span class="surname">Kelbrath</span></h1>
    <p class="person-role">PARTNER</p>
  </div>

  <span class="divider"></span>

  <ul class="contacts">
    <li>
      <svg viewBox="0 0 16 16" aria-hidden="true"><path d="M3.5 1.5l2.6 2.8-1.5 1.8c.9 2 2.4 3.5 4.4 4.4l1.8-1.5 2.8 2.6-1.6 2.4C6.8 13.8 2.2 9.2 1.1 3.1z"/></svg>
      <span>0461 738 524</span>
    </li>
    <li>
      <svg viewBox="0 0 16 16" aria-hidden="true"><path d="M1 4h14v1.2L8 9.3 1 5.2z"/><path d="M1 6.6l7 4.1 7-4.1V13H1z"/></svg>
      <span>doran@kbtlaw.co</span>
    </li>
    <li>
      <svg viewBox="0 0 16 16" aria-hidden="true"><circle cx="8" cy="8" r="6.5" fill="none" stroke="#f04a50" stroke-width="1.3"/><ellipse cx="8" cy="8" rx="2.8" ry="6.5" fill="none" stroke="#f04a50" stroke-width="1.1"/><path d="M1.5 8h13M2.5 5h11M2.5 11h11" stroke="#f04a50" stroke-width="1"/></svg>
      <span>www.kbtlaw.co</span>
    </li>
    <li>
      <svg viewBox="0 0 16 16" aria-hidden="true"><path d="M8 0.8a5.4 5.4 0 0 0-5.4 5.4C2.6 10 8 15.4 8 15.4s5.4-5.4 5.4-9.2A5.4 5.4 0 0 0 8 0.8zm0 7.5a2.1 2.1 0 1 1 0-4.2 2.1 2.1 0 0 1 0 4.2z"/></svg>
      <span>Level 3, 118 Wendmore Street<br>Sydney NSW 2000</span>
    </li>
  </ul>

  <svg class="footer-band" viewBox="0 0 757 12" preserveAspectRatio="none" aria-hidden="true">
    <polygon points="0,0 372,0 360,12 0,12" fill="#1b1b1b"/>
    <polygon points="390,0 757,0 757,12 378,12" fill="#f04a50"/>
  </svg>
</section>

</body>
</html>
```